Quote Cards With KB May 2025 for Instagram

I would like to put these quotes over one of the pictures attached; Instagram (new size: 4:5 (1080 x 1350 pixels) One Quote per picture, and I want the quote to be bold or easy to read as well. I provided a few reference graphics that I really like as examples below. In very small letters at the bottom add @KBHarlowOnline

All of the pictures are attached; you can pick any photo and add one quote to it; but no stock photography

```html
<!DOCTYPE html>
<html lang="en">
<head>
<meta charset="utf-8">
<title>Quote Cards — KB Hormone Series</title>
<link rel="stylesheet" href="https://fonts.googleapis.com/css2?family=Oswald:wght@400;500;600&display=swap">
<style>
  :root {
    --canvas-dark: #5f5f5f;
    --canvas-light: #8a8a8a;
    --magenta: #d0046a;
    --magenta-deep: #b8065e;
    --pink: #e8267f;
    --pink-soft: #f4c4da;
    --blush-text: #ece0e6;
    --white: #ffffff;
    --card-w: 930px;
    --card-h: 1167px;
  }
  * { margin: 0; padding: 0; box-sizing: border-box; }
  html, body { width: 1200px; height: 3892px; overflow: hidden; }
  body {
    position: relative;
    background: radial-gradient(ellipse at center, var(--canvas-light) 0%, var(--canvas-dark) 100%);
    font-family: "Oswald", sans-serif;
  }
  .quote-card {
    position: absolute;
    left: 135px;
    width: var(--card-w);
    height: var(--card-h);
    overflow: hidden;
    box-shadow: 0 18px 50px rgba(0,0,0,0.45);
  }
  .quote-card--tired { top: 131px; background: linear-gradient(180deg, var(--magenta) 40%, var(--pink) 100%); }
  .quote-card--weight { top: 1365px; }
  .quote-card--belly { top: 2596px; }

  .photo { position: absolute; left: 0; top: 0; width: 100%; }

  .condensed { transform-origin: center top; }

  /* Card 1 */
  .quote-card--tired .photo {
    height: 560px;
    background: linear-gradient(180deg, #6b4a34 0%, #8a644a 45%, #2a2220 75%, #c98a6a 100%);
  }
  .tired-panel {
    position: absolute;
    left: 29px; top: 465px;
    width: 875px; height: 702px;
    background: linear-gradient(180deg, var(--magenta) 0%, var(--pink) 60%, var(--pink) 100%);
  }
  .headline {
    position: absolute; left: 0; width: 100%;
    text-align: center; color: var(--white);
    font-weight: 600; text-transform: uppercase;
    letter-spacing: -1px;
  }
  .quote-card--tired .headline {
    top: 538px;
    font-size: 90px; line-height: 104px;
    transform: scaleX(0.85);
  }

  .handle {
    position: absolute; left: 0; width: 100%;
    top: 1080px;
    text-align: center;
    font-family: "Oswald", sans-serif; font-weight: 500;
    font-size: 28px; letter-spacing: 0.5px; color: var(--white);
  }

  /* Card 2 */
  .quote-card--weight .photo {
    height: 100%;
    background: linear-gradient(135deg, #f0702a 0%, #5a3fb0 35%, #3a2a8c 55%, #d0307a 80%, #a3045a 100%);
  }
  .weight-fade {
    position: absolute; left: 0; bottom: 0; width: 100%; height: 640px;
    background: linear-gradient(180deg, rgba(176,6,100,0) 0%, rgba(176,6,100,0.85) 30%, var(--magenta-deep) 70%, var(--pink) 100%);
  }
  .label-box {
    position: absolute;
    display: flex; align-items: center; justify-content: center;
    font-weight: 600; text-transform: uppercase;
    font-size: 60px; letter-spacing: -1px;
  }
  .label-box span { display: inline-block; }
  .quote-card--weight .label-box {
    left: 100px; top: 588px; width: 731px; height: 98px;
    background: var(--magenta); color: var(--white);
  }
  .quote-card--weight .label-box span { transform: scaleX(0.94); }
  .quote-card--weight .headline {
    top: 706px;
    font-size: 70px; line-height: 92px;
    transform: scaleX(0.87);
  }

  /* Card 3 */
  .quote-card--belly .photo {
    height: 100%;
    background: linear-gradient(180deg, #e6e6e6 0%, #d8d6d4 35%, #c8c2c0 50%, var(--pink-soft) 70%, #e35a98 88%, #d61a70 100%);
  }
  .quote-card--belly .label-box {
    left: 97px; top: 585px; width: 737px; height: 103px;
    background: var(--white); color: var(--magenta);
  }
  .quote-card--belly .label-box span { transform: scaleX(0.93); }
  .hormonal {
    position: absolute; left: 0; width: 100%; top: 728px;
    text-align: center; text-transform: uppercase;
    font-weight: 600; font-size: 90px; letter-spacing: -1px;
    color: var(--blush-text);
    text-shadow: 0 3px 6px rgba(90,0,40,0.45);
    transform: scaleX(0.85);
  }
  .cta {
    position: absolute; left: 0; width: 100%; top: 846px;
    text-align: center; color: var(--white);
    font-weight: 400; font-size: 60px; line-height: 83px; letter-spacing: -1px;
    text-shadow: 0 3px 6px rgba(90,0,40,0.45);
    transform: scaleX(1.02);
  }
  .cta u { text-decoration-thickness: 3px; text-underline-offset: 8px; }
</style>
</head>
<body>

  <section class="quote-card quote-card--tired">
    <div class="photo" role="img" aria-label="Photo of KB in a black sheer striped top pointing down, in a wooden kitchen"></div>
    <div class="tired-panel"></div>
    <p class="headline condensed">Tired. Moody.<br>Stubborn belly fat.<br>Your hormones are<br>screaming for help!<br>Let’s fix that.</p>
    <p class="handle">@KBHarlowOnline</p>
  </section>

  <section class="quote-card quote-card--weight">
    <div class="photo" role="img" aria-label="Photo of KB in a magenta wrap dress on a stage with neon lights and a golden statue"></div>
    <div class="weight-fade"></div>
    <div class="label-box"><span>That stubborn weight?</span></div>
    <p class="headline condensed">It’s not your fault.&nbsp; Your<br>hormones are to blame<br>and you’re not alone;<br>but there is a fix.</p>
    <p class="handle">@KBHarlowOnline</p>
  </section>

  <section class="quote-card quote-card--belly">
    <div class="photo" role="img" aria-label="Photo of KB in a white cropped sweater dancing in a bright white kitchen"></div>
    <div class="label-box"><span>Your belly isn’t fat...</span></div>
    <p class="hormonal condensed">It’s hormonal.</p>
    <p class="cta condensed">And here’s how to fix it. Comment<br><u>HORMONES</u> if nothing is working.</p>
    <p class="handle">@KBHarlowOnline</p>
  </section>

</body>
</html>
```